Spiritual Healing bussiness needs logo/business card

Simple, clean looking logo/card
For spiritual business with healing services and occult rituals

Contact Information for Business Card

Needs my name: Tobin Varley
Business name: Lantern Healing Shop
Services provided and worded in this way:

Reiki Healing
Tarot
Oils
Rituals Of Change

Can look occult like but with light energy.

Colors
0255a3
3276b5
85abd2
33a6d7
85cae6
0292cd

```html
<!DOCTYPE html>
<html lang="en">
<head>
<meta charset="utf-8">
<title>Lantern Healing Shop – Business Card</title>
<link rel="stylesheet" href="https://fonts.googleapis.com/css2?family=Oswald:wght@500&family=Lato:wght@400&display=swap">
<style>
  :root {
    --backdrop: #8a5a33;
    --royal: #0255a3;
    --mid-blue: #3276b5;
    --pale-blue: #85abd2;
    --sky: #33a6d7;
    --ice: #85cae6;
    --cyan: #0292cd;
    --white: #ffffff;
    --grey-text: #5a5a5a;
  }
  * { margin: 0; padding: 0; box-sizing: border-box; }
  html, body { width: 1200px; height: 900px; overflow: hidden; }
  body { background: var(--backdrop); position: relative; font-family: "Lato", sans-serif; }

  .card {
    position: absolute;
    width: 556px;
    height: 343px;
    overflow: hidden;
    box-shadow: 3px 4px 8px rgba(0,0,0,0.45);
  }
  .card-front { left: 330px; top: 90px; background: var(--white); }
  .card-back { left: 331px; top: 470px; background: var(--royal); }

  .wave { position: absolute; inset: 0; width: 100%; height: 100%; }

  .brand { position: absolute; left: 0; top: 40px; width: 264px; text-align: center; }
  .brand-dot {
    width: 76px; height: 76px; border-radius: 50%;
    background: var(--royal); margin: 0 auto 22px;
  }
  .brand-name {
    font-family: "Oswald", sans-serif; font-weight: 500;
    font-size: 25px; letter-spacing: 0.3px; line-height: 1;
    color: var(--royal); white-space: nowrap;
  }
  .brand-tagline {
    margin-top: 5px; font-size: 10.5px; letter-spacing: 0.2px;
    color: var(--grey-text); white-space: nowrap;
  }

  .holder-name {
    position: absolute; right: 34px; top: 172px;
    font-family: "Oswald", sans-serif; font-weight: 500;
    font-size: 21px; color: var(--white);
  }
  .contact { position: absolute; right: 30px; top: 214px; text-align: right; color: var(--white); font-size: 15.5px; }
  .contact-line { display: flex; align-items: center; justify-content: flex-end; gap: 2px; height: 22px; }
  .contact-icon { width: 18px; height: 18px; }

  .services {
    position: absolute; right: 27px; top: 296px;
    display: flex; align-items: center; gap: 11px;
    color: var(--white); font-size: 16px; white-space: nowrap;
  }
  .services .sep { width: 7px; height: 7px; border-radius: 50%; background: var(--white); }

  .back-mark { position: absolute; inset: 0; display: flex; flex-direction: column; align-items: center; justify-content: center; }
  .back-dot { width: 120px; height: 120px; border-radius: 50%; background: var(--ice); margin-bottom: 22px; }
  .back-name { font-family: "Oswald", sans-serif; font-weight: 500; font-size: 26px; color: var(--white); }
</style>
</head>
<body>

<section class="card card-front">
  <svg class="wave" viewBox="0 0 556 343" preserveAspectRatio="none" aria-hidden="true">
    <path d="M0 218 C60 262 110 286 170 280 C280 268 340 90 470 80 C510 78 540 84 556 88 L556 92 C540 88 510 82 470 86 C345 98 285 276 170 288 C110 294 55 270 0 236 Z" fill="var(--cyan)"/>
    <path d="M0 240 C60 276 115 296 175 290 C290 278 350 112 470 98 C510 94 540 102 556 110 L556 343 L0 343 Z" fill="var(--royal)"/>
  </svg>

  <div class="brand">
    <div class="brand-dot"></div>
    <div class="brand-name">LANTERN HEALING SHOP</div>
    <div class="brand-tagline">HEALING SERVICES &amp; OCCULT RITUALS</div>
  </div>

  <div class="holder-name">TOBIN VARLEY</div>

  <div class="contact">
    <div class="contact-line">044-987 654 321
      <svg class="contact-icon" viewBox="0 0 18 18" aria-hidden="true">
        <circle cx="9" cy="9" r="8" fill="none" stroke="var(--white)" stroke-width="1.3"/>
        <path d="M5 8 Q9 4.5 13 8 L12 9 L10.6 8 L10.6 7 Q9 6.4 7.4 7 L7.4 8 L6 9 Z M6 10 H12 V12.5 H6 Z" fill="var(--white)"/>
      </svg>
    </div>
    <div class="contact-line">hello@lanternmail.com
      <svg class="contact-icon" viewBox="0 0 18 18" aria-hidden="true">
        <circle cx="9" cy="9" r="8" fill="none" stroke="var(--white)" stroke-width="1.3"/>
        <rect x="4.8" y="6" width="8.4" height="6" fill="var(--white)"/>
        <path d="M4.8 6 L9 9.3 L13.2 6" fill="none" stroke="var(--royal)" stroke-width="0.9"/>
      </svg>
    </div>
  </div>

  <div class="services">
    <span>Reiki Healing</span><span class="sep"></span>
    <span>Tarot</span><span class="sep"></span>
    <span>Oils</span><span class="sep"></span>
    <span>Rituals Of Change</span>
  </div>
</section>

<section class="card card-back">
  <div class="back-mark">
    <div class="back-dot"></div>
    <div class="back-name">LANTERN HEALING SHOP</div>
  </div>
</section>

</body>
</html>
```